Harborline Business Card Designs***

WE ARE A FULL SERVICE FACILITY. ALL KINDS OF CAR/ TRK, REPAIR. CUSTOM WHEELS & TIRES. BRAKES, MUFFLERS, SHOCK, STRUTS...BATTERIES, STARTERS, ATERNATORS, TUNE UPS (WE DO IT ALL) ESTABLISHED IN 2004, LOCALLY OWNED AND OPERATED.... I AM OPEN TO SUGGESTIONS AS WELL ON ANY IDEAS

Contact Information for Business Card

WE DO COMPLETE AUTO REPAIR AND WHEELS, TIRES AND ACCESSORIES AT OUR STORE. I NAME OF SHOP (HARBORLINE AUTOMOTIVE GROUP) WOULD LIKE OUR EMAIL ON IT (HARBORLINEAUTOGROUP@QUVIX.NET) PHONE NUMBER 567-302-GEAR (4327) BUSINESS HOURS MON- FRI 7:30-5 SNAPGRID LOGO WITH (@HARBORLINE_AUTO_WESTRIDGE) WEBSITE (KESTRELROADWORKS.NET)FRIENDLOOP LOGO W/ (FRIENDLOOP.NET/HARBORLINEAUTOMOTIVE) AN A+/ QCR LOGO (THE LITTLE TORCH)... MAYBE EVEN EST.2004 INSIDE OF A "POW SIGN" (UNLESS IT GETS TO CLUTTERED) AND ON THE BACK OF THE CARD MAYBE A FAINT PICTURE OF "SOMETHING" IN BACKGROUND BUT STILL BE ABLE TO SEE THE ESTIMATE WE WRITE ON THE BACK. I WOULD LIKE ON THE BACK, DOWN IN THE RIGHT HAND CORNER A SPOT FOR A DATE AND INT. WE ALSO EXCEPT: ORBA, TRUSTPLATE, KELMORE AND ZINCWAY

```html
<!DOCTYPE html>
<html lang="en">
<head>
<meta charset="utf-8">
<title>Harborline Automotive Group – Business Card</title>
<link rel="stylesheet" href="https://fonts.googleapis.com/css2?family=Roboto+Condensed:wght@400;700&family=Orbitron:wght@900&family=Michroma&display=swap">
<style>
  :root {
    --stage: #5f5145;
    --card: #efefef;
    --ink: #1b1b1b;
    --text: #3a3a3a;
    --brand-blue: #1a7fd0;
    --hours-blue: #3b3f9a;
    --burst: #1eaae6;
    --rule: #3a3a3a;
    --hint: #b9b9b9;
    --photo-a: #e4e4e6;
    --photo-b: #d2d3d8;
  }
  * { box-sizing: border-box; margin: 0; padding: 0; }
  html, body { width: 1200px; height: 1200px; overflow: hidden; }
  body { background: var(--stage); font-family: "Roboto Condensed", sans-serif; color: var(--text); position: relative; }

  .card {
    position: absolute; left: 232px; width: 736px; height: 440px;
    background: var(--card); overflow: hidden;
    box-shadow: 0 10px 18px rgba(0,0,0,.45);
  }
  .card--front { top: 90px; }
  .card--back { top: 650px; }

  .card__photo { position: absolute; inset: 0; }
  .card--front .card__photo { background: radial-gradient(ellipse at 40% 25%, var(--photo-b), var(--photo-a) 70%); }
  .card--back .card__photo { background: linear-gradient(180deg, var(--photo-b), var(--photo-a) 45%, var(--photo-b)); }
  .card__band { position: absolute; left: 0; right: 0; top: 184px; height: 130px; background: rgba(255,255,255,.55); }

  .brand { position: absolute; text-align: center; }
  .brand__script { font-family: "Roboto Condensed", sans-serif; font-weight: 700; color: var(--ink); }
  .brand__name { font-family: "Orbitron", sans-serif; font-weight: 900; color: var(--brand-blue); letter-spacing: 1px; line-height: 1; }
  .brand__sub { font-family: "Michroma", sans-serif; color: var(--ink); line-height: 1; white-space: nowrap; }

  .card--front .brand { left: 0; right: 0; top: 100px; }
  .card--front .brand__script { font-size: 28px; line-height: 1; }
  .card--front .brand__name { font-size: 50px; margin-top: 10px; }
  .card--front .brand__sub { font-size: 27px; margin-top: 12px; }
  .hours { font-size: 21px; color: var(--hours-blue); margin-top: 12px; letter-spacing: .2px; }

  .rule { position: absolute; height: 3px; background: linear-gradient(90deg, transparent, var(--rule) 15%, #777 50%, var(--rule) 85%, transparent); }
  .card--front .rule { left: 34px; right: 6px; top: 288px; }
  .card--back .rule { left: 34px; right: 6px; top: 317px; }

  .contact-row { position: absolute; left: 0; right: 0; display: flex; justify-content: center; align-items: center; font-size: 15px; color: var(--text); }
  .contact-row--one { top: 312px; }
  .contact-row--two { top: 364px; }
  .contact { display: flex; align-items: center; gap: 7px; padding: 0 12px; height: 40px; }
  .contact + .contact { border-left: 1px solid #888; }
  .contact svg { flex: none; }
  .contact__network { font-weight: 700; color: var(--ink); }
  .mark-square { width: 22px; height: 22px; background: #6b7d94; flex: none; }
  .badge { width: 30px; height: 36px; background: #8fa8b8; }

  .card--back .brand { left: 138px; top: 150px; text-align: left; }
  .card--back .brand__script { font-size: 24px; padding-left: 120px; }
  .card--back .brand__name { font-size: 38px; margin-top: 6px; }
  .card--back .brand__sub { font-size: 20px; margin-top: 8px; }
  .est-burst { position: absolute; left: 474px; top: 178px; width: 160px; height: 72px; }

  .payments { position: absolute; left: 84px; top: 340px; display: flex; gap: 8px; align-items: center; }
  .payment { display: flex; align-items: center; gap: 5px; height: 40px; padding: 0 7px; background: #fff; border: 1px solid #cfcfcf; font-size: 14px; font-weight: 700; color: var(--ink); }
  .payment__dot { width: 10px; height: 10px; background: var(--brand-blue); }

  .estimate { position: absolute; left: 518px; top: 340px; font-size: 17px; color: var(--ink); line-height: 1.35; }
  .estimate__hint { color: var(--hint); }
</style>
</head>
<body>

<section class="card card--front">
  <div class="card__photo" role="img" aria-label="Faint photo of a chrome engine bay with air cleaner"></div>
  <div class="brand">
    <div class="brand__script">Harborline</div>
    <div class="brand__name">HARBORLINE</div>
    <div class="brand__sub">AUTOMOTIVE GROUP</div>
    <div class="hours">BUSINESS HOURS MON- FRI 7:30-5</div>
  </div>
  <div class="rule"></div>

  <div class="contact-row contact-row--one">
    <div class="contact">
      <svg width="22" height="22" viewBox="0 0 24 24" aria-hidden="true"><path d="M6.6 10.8a15 15 0 0 0 6.6 6.6l2.2-2.2a1 1 0 0 1 1-.25 11.4 11.4 0 0 0 3.6.57 1 1 0 0 1 1 1V20a1 1 0 0 1-1 1A17 17 0 0 1 3 4a1 1 0 0 1 1-1h3.5a1 1 0 0 1 1 1c0 1.25.2 2.45.57 3.57a1 1 0 0 1-.25 1z" fill="#333"/></svg>
      <span>567-302-Gear (4327)</span>
    </div>
    <div class="contact">
      <svg width="22" height="22" viewBox="0 0 24 24" aria-hidden="true"><circle cx="12" cy="12" r="10" fill="none" stroke="#333" stroke-width="2"/><ellipse cx="12" cy="12" rx="4" ry="10" fill="none" stroke="#333" stroke-width="1.5"/><line x1="2" y1="12" x2="22" y2="12" stroke="#333" stroke-width="1.5"/></svg>
      <span>kestrelroadworks.net</span>
    </div>
    <div class="contact">
      <svg width="26" height="20" viewBox="0 0 26 20" aria-hidden="true"><rect x="1" y="1" width="24" height="18" fill="none" stroke="#333" stroke-width="2"/><path d="M1 1l12 10 12-10" fill="none" stroke="#333" stroke-width="2"/></svg>
      <span>harborlineautogroup@quvix.net</span>
    </div>
  </div>

  <div class="contact-row contact-row--two">
    <div class="contact">
      <span class="mark-square"></span>
      <span class="contact__network">SnapGrid</span>
      <span>harborline_auto_westridge</span>
    </div>
    <div class="contact">
      <span class="contact__network">FriendLoop</span>
      <span>harborlineautomotive</span>
    </div>
    <div class="contact">
      <span class="badge" aria-label="QCR A+ rating badge"></span>
    </div>
  </div>
</section>

<section class="card card--back">
  <div class="card__photo" role="img" aria-label="Faint photo of rows of chrome custom wheels"></div>
  <div class="card__band"></div>
  <div class="brand">
    <div class="brand__script">Harborline</div>
    <div class="brand__name">HARBORLINE</div>
    <div class="brand__sub">AUTOMOTIVE GROUP</div>
  </div>
  <svg class="est-burst" viewBox="0 0 160 72" aria-label="Established 2004">
    <polygon fill="var(--burst)" points="14,36 0,30 18,24 12,8 36,16 52,2 66,14 84,4 98,14 118,0 122,18 150,14 140,30 160,36 140,42 150,58 124,54 118,72 98,60 80,70 66,58 44,68 38,54 12,62 20,46"/>
    <text x="80" y="45" text-anchor="middle" font-family="Roboto Condensed, sans-serif" font-size="26" fill="#fff">EST.2004</text>
  </svg>
  <div class="rule"></div>

  <div class="payments">
    <div class="payment"><span class="payment__dot"></span>Zincway</div>
    <div class="payment">TrustPlate</div>
    <div class="payment">Orba</div>
    <div class="payment">Kelmore</div>
  </div>

  <div class="estimate">
    <div>DATE : <span class="estimate__hint">DD/MM/YYYY</span></div>
    <div>INT :</div>
  </div>
</section>

</body>
</html>
```